Business Card Design Project

Business Card
We are rebranding with a new logo
Industry/Entity Type
Business
Contact Information for Business Card
Dennis Morvale +61 487215963 dennis@quorv.com.au P.O. Box 872 Fernlow QLD 4309
Requirements
Must have
- Logo

```html
<!DOCTYPE html>
<html lang="en">
<head>
<meta charset="utf-8">
<title>Quorv International – Business Card</title>
<link rel="stylesheet" href="https://fonts.googleapis.com/css2?family=Varela+Round&family=Exo+2:wght@600&display=swap">
<style>
  :root {
    --page-bg: #e9e6e2;
    --card-bg: #1c1c1d;
    --card-edge: #2a2a2b;
    --accent-orange: #e8874a;
    --brand-blue: #4fb3dc;
    --emboss-grey: #8a8a8c;
    --emboss-dark: #5e5e60;
  }
  * { margin: 0; padding: 0; box-sizing: border-box; }
  html, body {
    width: 1200px;
    height: 800px;
    overflow: hidden;
    background: var(--page-bg);
  }
  .canvas {
    width: 1200px;
    height: 800px;
    display: flex;
    align-items: center;
    justify-content: center;
  }
  .business-card {
    width: 1000px;
    height: 580px;
    background: var(--card-bg);
    border-radius: 28px;
    border: 1px solid var(--card-edge);
    box-shadow: 0 18px 40px rgba(0,0,0,0.25);
    display: flex;
    flex-direction: column;
    align-items: center;
    padding-top: 120px;
  }
  .brand {
    display: flex;
    align-items: center;
    gap: 22px;
  }
  .brand-mark {
    width: 34px;
    height: 34px;
    border-radius: 50%;
    background: var(--brand-blue);
  }
  .brand-name {
    font-family: "Exo 2", sans-serif;
    font-weight: 600;
    font-size: 54px;
    letter-spacing: 6px;
    color: var(--brand-blue);
    text-transform: uppercase;
  }
  .holder-name {
    margin-top: 110px;
    font-family: "Varela Round", sans-serif;
    font-size: 44px;
    color: var(--emboss-dark);
    text-shadow: 0 1px 0 rgba(255,255,255,0.12), 0 -1px 0 rgba(0,0,0,0.6);
  }
  .contact-row {
    display: flex;
    gap: 70px;
    margin-top: 40px;
  }
  .contact-item {
    display: flex;
    align-items: center;
    gap: 12px;
    font-family: "Varela Round", sans-serif;
    font-size: 26px;
    color: var(--emboss-grey);
  }
  .contact-item + .contact-item { }
  .address { margin-top: 20px; }
  .icon { width: 26px; height: 26px; fill: var(--accent-orange); flex: none; }
</style>
</head>
<body>
<main class="canvas">
  <section class="business-card">
    <div class="brand">
      <span class="brand-mark"></span>
      <span class="brand-name">Quorv International</span>
    </div>

    <h1 class="holder-name">Dennis Morvale</h1>

    <div class="contact-row">
      <p class="contact-item phone">
        <svg class="icon" viewBox="0 0 24 24" aria-hidden="true"><path d="M3 7c0-2 4-4 9-4s9 2 9 4v2h-5V7H8v2H3z"/><path d="M6 11h12l2 9H4z"/><circle cx="12" cy="15.5" r="2.5" fill="#1c1c1d"/></svg>
        +61 487215963
      </p>
      <p class="contact-item email">
        <svg class="icon" viewBox="0 0 24 24" aria-hidden="true"><path d="M2 5h20v14H2z"/><path d="M2 5l10 8 10-8" fill="none" stroke="#1c1c1d" stroke-width="1.8"/></svg>
        dennis@quorv.com.au
      </p>
    </div>
    <p class="contact-item address">
      <svg class="icon" viewBox="0 0 24 24" aria-hidden="true"><path d="M12 2a7 7 0 0 0-7 7c0 5 7 13 7 13s7-8 7-13a7 7 0 0 0-7-7z"/><circle cx="12" cy="9" r="2.6" fill="#1c1c1d"/></svg>
      P.O. Box 872 Fernlow QLD 4309
    </p>
  </section>
</main>
</body>
</html>
```